uk based ecommerce website requires fresh look ,high quality look and feel

we are a web based company selling eco friendly ground reinforcement grids to diy and construction sectors
our existing website is www.pondermeshpaths.co.uk ,

we have already updated the logo so that is the branding sorted .so we need a ecommerce website that is very much up-to date in design and layout and which has content management system for ease of use so that we can add products and information as required.

Use current logo as reference for colour scheme.
www.pondermeshpaths.co.uk

The current website has 6 pages accessible through the navigation bar, I would now like 5 pages, removing the need for the Trade Enquiries page possibly have it with along with contact us.

Target Market(s)

construction industry , diy end users,
retail market, landscapers, gardeners

Industry/Entity Type

Construction

Font styles to use
Other font styles liked:
• logo font prometo

Colors
f78f20
9bcb3c

Requirements
Must have
• logo colours and logo design in website with cms responsive design for tablet and mobile devices
• expect content to work flawlessly and look great across all devices
• HTML 5 custom design with coding as required
• must have good experiance in ecommerce website design
• eye catching, high quality look and feel and very user friedly ,very up-to date.
Nice to have
• picture slider show
• explain in writing what exactly i am getting in my ecommerce website
Should not have
• plain , basic design , old fashion looking ,cheap look

```html
<!DOCTYPE html>
<html lang="en">
<head>
<meta charset="utf-8">
<title>Pondermesh Ground Solutions</title>
<link rel="stylesheet" href="https://fonts.googleapis.com/css2?family=Rajdhani:wght@500;600;700&family=Raleway:wght@400;500;600;700&display=swap">
<style>
:root{
  --orange:#f78f20;
  --orange-dark:#e87a10;
  --green:#9bcb3c;
  --green-dark:#7fb12a;
  --ink:#2b2b2b;
  --text:#555;
  --grey-bg:#ececec;
  --dark:#262626;
  --darker:#1c1c1c;
  --white:#fff;
}
*{box-sizing:border-box;margin:0;padding:0}
html,body{width:1200px;height:2862px;overflow:hidden}
body{position:relative;background:var(--white);font-family:"Raleway",Arial,sans-serif;color:var(--text)}
.abs{position:absolute}
.heading{font-family:"Rajdhani","Arial Narrow",sans-serif}

/* header */
.site-header{left:0;top:0;width:1200px;height:143px;background:var(--white)}
.brand{left:99px;top:40px;display:flex;align-items:center;gap:14px}
.brand-mark{width:52px;height:52px;background:var(--green)}
.brand-name{font-family:"Rajdhani",sans-serif;font-weight:700;font-size:38px;color:var(--orange);letter-spacing:1px}
.contact-item{top:46px;display:flex;gap:14px;align-items:flex-start}
.contact-item .dot{width:44px;height:44px;border-radius:50%;display:flex;align-items:center;justify-content:center}
.contact-item .label{font-size:19px;color:var(--ink);font-weight:500}
.contact-item .value{font-size:18px;color:var(--ink);margin-top:6px}
.contact-item.service .value{font-size:16px}

/* nav */
.main-nav{left:0;top:143px;width:1200px;height:67px;background:linear-gradient(var(--orange),var(--orange-dark))}
.main-nav ul{position:absolute;left:0;top:0;width:1200px;height:67px;list-style:none}
.main-nav li{position:absolute;top:0;height:67px;line-height:67px;color:var(--white);font-size:13px;text-transform:uppercase;text-align:center;white-space:nowrap}
.main-nav li.active{background:var(--green)}
.nav-search{left:967px;top:0;width:136px;height:67px;background:#3a3a3a;color:#eee;font-size:14px;padding:0 18px;display:flex;align-items:center;justify-content:space-between}

/* hero */
.hero{left:0;top:210px;width:1200px;height:559px;background:linear-gradient(100deg,#4a4a3e 0%,#6b5e45 35%,#c7823d 70%,#e9a04b 100%)}
.hero-title{right:100px;top:112px;font-size:38px;font-weight:700;color:var(--orange);letter-spacing:1px;text-transform:uppercase;white-space:nowrap}
.hero-text{right:100px;top:212px;width:580px;text-align:right;font-size:18px;line-height:30px;color:var(--white)}
.btn-pill{border-radius:30px;color:var(--white);background:var(--orange);border:2px solid #ffb366;display:flex;align-items:center;justify-content:center}
.hero-btn{left:933px;top:300px;width:168px;height:54px;font-size:18px}
.hero-arrow{top:240px}

/* intro */
.intro-panel{left:99px;top:708px;width:1004px;height:603px;background:var(--white);box-shadow:0 0 18px rgba(0,0,0,.18);border-top:4px solid var(--orange)}
.section-title{width:100%;text-align:center;font-family:"Rajdhani",sans-serif;font-weight:600;color:var(--ink);font-size:34px;letter-spacing:1px;text-transform:uppercase}
.ornament{left:50%;margin-left:-50px}
.intro-text{left:60px;top:138px;width:884px;text-align:center;font-size:14px;line-height:29px}
.feature{top:212px;width:290px;text-align:center}
.hex{margin:0 auto;width:214px;height:188px;display:block}
.feature h3{font-size:17px;font-weight:600;color:var(--ink);margin-top:32px;text-transform:uppercase}
.feature p{font-size:13px;line-height:23px;margin-top:14px}
.feature .more{display:block;font-size:13px;color:var(--orange);font-weight:600;margin-top:16px}

/* promo band */
.promo-band{left:0;top:1311px;width:1200px;height:435px;background:linear-gradient(#3a3733,#1f1e1c)}
.promo-band h2{font-size:26px;color:var(--white);font-weight:600;top:67px}
.promo-card{top:112px;width:475px;height:266px;overflow:hidden}
.promo-card .photo{left:0;top:0;width:300px;height:266px}
.promo-card svg.panel{left:0;top:0}
.promo-card .copy{left:282px;top:20px;width:180px;color:var(--white)}
.promo-card .copy h4{font-size:17px;font-weight:600;line-height:26px}
.promo-card ul{list-style:none;margin-top:16px}
.promo-card li{font-size:13px;line-height:28px;display:flex;align-items:center;gap:10px}
.promo-card li i{width:11px;height:11px;border-radius:50%;background:var(--white);display:inline-block}
.promo-card .info{margin-top:14px;width:98px;height:34px;border-radius:20px;background:var(--white);color:var(--ink);font-size:12px;font-weight:600;display:flex;align-items:center;justify-content:center}

/* categories */
.categories{left:0;top:1746px;width:1200px;height:492px;background:var(--grey-bg)}
.product{top:147px;width:233px;height:292px;background:var(--white);border:1px solid #d6d6d6}
.product .photo{left:8px;top:5px;width:217px;height:163px}
.product h5{top:196px;width:100%;text-align:center;font-size:14px;font-weight:600;color:var(--ink)}
.product .price{left:20px;top:238px;font-size:15px;color:var(--ink)}
.product .options{left:92px;top:229px;width:122px;height:38px;background:var(--orange);color:var(--white);font-size:13px;display:flex;align-items:center;justify-content:center;border:1px solid #ffb366}

/* cta */
.cta{left:0;top:2238px;width:1200px;height:256px;background:linear-gradient(#d9821f,#c9742a 50%,#e79b4c)}
.cta .line1{top:54px;width:100%;text-align:center;font-size:27px;font-weight:700;color:var(--white);letter-spacing:1px}
.cta .line2{top:108px;width:100%;text-align:center;font-size:26px;font-weight:600;color:var(--white);letter-spacing:1px}
.cta .email-btn{left:481px;top:160px;width:238px;height:54px;border-radius:30px;background:var(--white);color:var(--ink);font-size:16px;font-weight:500;display:flex;align-items:center;justify-content:center}

/* footer */
.site-footer{left:0;top:2494px;width:1200px;height:297px;background:var(--dark)}
.footer-brand{left:99px;top:115px;display:flex;align-items:center;gap:12px}
.footer-brand .mark{width:46px;height:46px;background:var(--white)}
.footer-brand .name{font-family:"Rajdhani",sans-serif;font-weight:700;font-size:32px;color:var(--white)}
.footer-col h6{font-size:18px;font-weight:600;color:var(--orange);text-transform:uppercase;letter-spacing:.5px}
.quick-links{list-style:none;margin-top:24px}
.quick-links li{font-size:12px;color:#ddd;line-height:26px}
.contact-line{display:flex;gap:12px;color:#ddd;font-size:12px;line-height:18px;margin-top:20px}
.form-field{border:1px solid #8a8a8a;border-radius:3px;color:#ccc;font-size:11px;padding:8px}
.send{left:832px;top:217px;width:120px;height:38px;background:var(--orange);color:var(--white);font-size:11px;display:flex;align-items:center;justify-content:center;border:1px solid #ffb366}

/* bottom bar */
.bottom-bar{left:0;top:2791px;width:1200px;height:71px;background:var(--orange)}
.copyright{left:99px;top:26px;font-size:14px;color:var(--white)}
.pay{top:22px;width:44px;height:28px;background:var(--white);border-radius:3px}
.social{top:18px;width:34px;height:34px;border-radius:50%;border:2px solid var(--white)}
</style>
</head>
<body>

<header class="site-header abs">
  <div class="brand abs"><span class="brand-mark"></span><span class="brand-name">PONDERMESH</span></div>
  <div class="contact-item abs" style="left:588px">
    <div class="dot" style="background:var(--orange)">
      <svg width="22" height="22" viewBox="0 0 24 24"><path d="M6.6 10.8a15 15 0 006.6 6.6l2.2-2.2c.3-.3.7-.4 1-.2 1.1.4 2.3.6 3.6.6.6 0 1 .4 1 1V20c0 .6-.4 1-1 1A17 17 0 013 4c0-.6.4-1 1-1h3.5c.6 0 1 .4 1 1 0 1.3.2 2.5.6 3.6.1.3 0 .7-.2 1z" fill="#fff"/></svg>
    </div>
    <div><div class="label">Call Us:</div><div class="value">0123-456-7890</div></div>
  </div>
  <div class="contact-item service abs" style="left:818px">
    <div class="dot" style="background:var(--green)">
      <svg width="22" height="22" viewBox="0 0 24 24"><rect x="3" y="6" width="18" height="12" rx="1.5" fill="none" stroke="#fff" stroke-width="2"/><path d="M3 7l9 6 9-6" fill="none" stroke="#fff" stroke-width="2"/></svg>
    </div>
    <div><div class="label">Service:</div><div class="value">24 HOUR MESSAGING SERVICE</div></div>
  </div>
</header>

<nav class="main-nav abs">
  <ul>
    <li class="active" style="left:99px;width:124px">Home</li>
    <li style="left:223px;width:100px">Shop</li>
    <li style="left:332px;width:110px">About Us</li>
    <li style="left:465px;width:180px">Ground Solutions</li>
    <li style="left:666px;width:130px">Pondermesh</li>
    <li style="left:820px;width:120px">Contact Us</li>
  </ul>
  <div class="nav-search abs"><span>Search...</span>
    <svg width="16" height="16" viewBox="0 0 24 24"><circle cx="10" cy="10" r="6.5" fill="none" stroke="#fff" stroke-width="3"/><path d="M15 15l6 6" stroke="#fff" stroke-width="3"/></svg>
  </div>
</nav>

<section class="hero abs" role="img" aria-label="Runner on a gravel path through golden grass at sunset">
  <svg class="hero-arrow abs" style="left:28px" width="24" height="48" viewBox="0 0 24 48"><path d="M20 4L4 24l16 20" fill="none" stroke="#fff" stroke-width="2"/></svg>
  <svg class="hero-arrow abs" style="right:28px" width="24" height="48" viewBox="0 0 24 48"><path d="M4 4l16 20-16 20" fill="none" stroke="#fff" stroke-width="2"/></svg>
  <h1 class="hero-title heading abs">StoneWeave makes walking on it easy</h1>
  <p class="hero-text abs">Stabilised Gravel Paving grids combines purpose designed Cellular reinforcement Pavers with the natural appearance</p>
  <div class="hero-btn btn-pill abs">Read More</div>
</section>

<section class="intro-panel abs">
  <h2 class="section-title abs" style="top:42px">Pondermesh Eco Solutions Ltd</h2>
  <svg class="ornament abs" style="top:98px" width="100" height="12" viewBox="0 0 100 12"><path d="M0 6h22M40 6h6M54 6h6M78 6h22" stroke="#f78f20" stroke-width="2"/><circle cx="31" cy="6" r="4.5" fill="none" stroke="#f78f20" stroke-width="2"/><circle cx="50" cy="6" r="4.5" fill="none" stroke="#f78f20" stroke-width="2"/><circle cx="69" cy="6" r="4.5" fill="none" stroke="#f78f20" stroke-width="2"/></svg>
  <p class="intro-text abs">Stabilised Gravel Paving grids combines purpose designed Cellular reinforcement Pavers with the natural appearance, strength, security and free draining characteristics of a loose aggregate surface</p>

  <div class="feature abs" style="left:10px">
    <svg class="hex" viewBox="0 0 214 188" role="img" aria-label="Orange geotextile membrane icon"><polygon points="53,2 161,2 212,94 161,186 53,186 2,94" fill="#fff" stroke="#f78f20" stroke-width="3"/><polygon points="60,14 154,14 199,94 154,174 60,174 15,94" fill="#f78f20"/></svg>
    <h3>Geotextile Membranes</h3>
    <p>Woven geotextiles are used to separate the sub base from the sub grade and prevent intermixing of construction layers.</p>
    <span class="more">READ MORE &gt;&gt;</span>
  </div>
  <div class="feature abs" style="left:336px">
    <svg class="hex" viewBox="0 0 214 188" role="img" aria-label="Photo of metal garden edging set into lawn"><polygon points="53,2 161,2 212,94 161,186 53,186 2,94" fill="#fff" stroke="#9bcb3c" stroke-width="3"/><defs><linearGradient id="g2" x1="0" y1="0" x2="1" y2="1"><stop offset="0" stop-color="#6f8f3a"/><stop offset="1" stop-color="#b9b9b0"/></linearGradient></defs><polygon points="60,14 154,14 199,94 154,174 60,174 15,94" fill="url(#g2)"/></svg>
    <h3>Garden Edging</h3>
    <p>Woven geotextiles are used to separate the sub base from the sub grade and prevent intermixing of construction layers.</p>
    <span class="more">READ MORE &gt;&gt;</span>
  </div>
  <div class="feature abs" style="left:680px">
    <svg class="hex" viewBox="0 0 214 188" role="img" aria-label="Photo of a wheeled walker on a gravel surface"><polygon points="53,2 161,2 212,94 161,186 53,186 2,94" fill="#fff" stroke="#9bcb3c" stroke-width="3"/><defs><linearGradient id="g3" x1="0" y1="0" x2="0" y2="1"><stop offset="0" stop-color="#5a5a5a"/><stop offset="1" stop-color="#a8a39a"/></linearGradient></defs><polygon points="60,14 154,14 199,94 154,174 60,174 15,94" fill="url(#g3)"/></svg>
    <h3>Light Domestic Driveways</h3>
    <p>Woven geotextiles are used to separate the sub base from the sub grade and prevent intermixing of construction layers.</p>
    <span class="more">READ MORE &gt;&gt;</span>
  </div>
</section>

<section class="promo-band abs" role="region" aria-label="Gravel driveways and ground reinforcement">
  <h2 class="abs" style="left:99px">Gravel Driveways</h2>
  <h2 class="abs" style="left:626px">Ground Reinforcement</h2>

  <div class="promo-card abs" style="left:99px">
    <div class="photo abs" role="img" aria-label="Car parked on a gravel driveway" style="background:linear-gradient(135deg,#7fa9d6,#b9c2c8 50%,#8b8170)"></div>
    <svg class="panel abs" width="475" height="266" viewBox="0 0 475 266"><path d="M252 0C200 60 290 100 230 150 190 190 250 230 240 266H475V0z" fill="#fff"/><path d="M264 0C212 60 302 100 242 150 202 190 262 230 252 266H475V0z" fill="#f78f20"/></svg>
    <div class="copy abs">
      <h4>There is an immense choice:</h4>
      <ul><li><i></i>Choice for resurfacing</li><li><i></i>Good deterrent</li><li><i></i>Crunching noise</li><li><i></i>Ground reinforcement</li></ul>
      <div class="info">MORE INFO</div>
    </div>
  </div>

  <div class="promo-card abs" style="left:626px">
    <div class="photo abs" role="img" aria-label="Gravel-filled reinforcement grid beside planting" style="background:linear-gradient(160deg,#4f8a3a,#9a9a9a 55%,#3e3e3e)"></div>
    <svg class="panel abs" width="475" height="266" viewBox="0 0 475 266"><path d="M252 0C200 60 290 100 230 150 190 190 250 230 240 266H475V0z" fill="#fff"/><path d="M264 0C212 60 302 100 242 150 202 190 262 230 252 266H475V0z" fill="#9bcb3c"/></svg>
    <div class="copy abs">
      <h4>There is an immense choice:</h4>
      <ul><li><i></i>Choice for resurfacing</li><li><i></i>Good deterrent</li><li><i></i>Crunching noise</li><li><i></i>Ground reinforcement</li></ul>
      <div class="info">MORE INFO</div>
    </div>
  </div>
</section>

<section class="categories abs">
  <h2 class="section-title abs" style="top:40px">Choose Your Category</h2>
  <svg class="ornament abs" style="top:94px" width="100" height="12" viewBox="0 0 100 12"><path d="M0 6h22M40 6h6M54 6h6M78 6h22" stroke="#f78f20" stroke-width="2"/><circle cx="31" cy="6" r="4.5" fill="none" stroke="#f78f20" stroke-width="2"/><circle cx="50" cy="6" r="4.5" fill="none" stroke="#f78f20" stroke-width="2"/><circle cx="69" cy="6" r="4.5" fill="none" stroke="#f78f20" stroke-width="2"/></svg>

  <div class="product abs" style="left:99px">
    <div class="photo abs" role="img" aria-label="Membrane laid on ground beside a wooden fence" style="background:linear-gradient(#8fa2b4,#7a6a4e 45%,#4a4a4a)"></div>
    <h5 class="abs">GEOTEXTILE MEMBRANES</h5><span class="price abs">£ 37.49</span><div class="options abs">Choose Options</div>
  </div>
  <div class="product abs" style="left:355px">
    <div class="photo abs" role="img" aria-label="Close view of gravel inside black grid cells" style="background:linear-gradient(#b5b5b5,#6a6a6a 60%,#2a2a2a)"></div>
    <h5 class="abs">LIGHT DOMESTIC DRIVE</h5><span class="price abs">£ 37.49</span><div class="options abs">Choose Options</div>
  </div>
  <div class="product abs" style="left:611px">
    <div class="photo abs" role="img" aria-label="Green grid being laid on a roadside site" style="background:linear-gradient(#7a9a5a,#8b6b5a 45%,#5a9a6a)"></div>
    <h5 class="abs">HEAVY DOMESTIC DRIVE</h5><span class="price abs">£ 37.49</span><div class="options abs">Choose Options</div>
  </div>
  <div class="product abs" style="left:866px">
    <div class="photo abs" role="img" aria-label="Workers installing grids on a commercial car park" style="background:linear-gradient(#c9d3dc,#b8aa96 50%,#6a6258)"></div>
    <h5 class="abs">COMMERCIAL PARKING</h5><span class="price abs">£ 37.49</span><div class="options abs">Choose Options</div>
  </div>
</section>

<section class="cta abs" role="img" aria-label="Warm toned country road background">
  <p class="line1 heading abs">NEED HELP / ADVICE OR WANT A QUOTE?</p>
  <p class="line2 heading abs">CALL US ON: 0800-555-0199</p>
  <div class="email-btn abs">CONTACT US BY EMAIL</div>
</section>

<footer class="site-footer abs">
  <div class="footer-brand abs"><span class="mark"></span><span class="name">PONDERMESH</span></div>

  <div class="footer-col abs" style="left:374px;top:52px">
    <h6>Quick Link</h6>
    <ul class="quick-links"><li>&gt;&nbsp; Home</li><li>&gt;&nbsp; About Us</li><li>&gt;&nbsp; Ground Solutions</li><li>&gt;&nbsp; Pondermesh</li><li>&gt;&nbsp; Our Services</li><li>&gt;&nbsp; Contact Us</li></ul>
  </div>

  <div class="footer-col abs" style="left:559px;top:52px;width:230px">
    <h6>Contact Us</h6>
    <div class="contact-line" style="margin-top:24px">
      <svg width="14" height="18" viewBox="0 0 14 18"><path d="M7 0a7 7 0 00-7 7c0 5 7 11 7 11s7-6 7-11a7 7 0 00-7-7z" fill="#f78f20"/><circle cx="7" cy="7" r="2.5" fill="#262626"/></svg>
      <span>PONDERMESH ECO SOLUTIONS<br>4th Floor, 18 Orchard Lane,<br>London, E1 4XY.</span>
    </div>
    <div class="contact-line">
      <svg width="14" height="14" viewBox="0 0 24 24"><path d="M6.6 10.8a15 15 0 006.6 6.6l2.2-2.2c.3-.3.7-.4 1-.2 1.1.4 2.3.6 3.6.6.6 0 1 .4 1 1V20c0 .6-.4 1-1 1A17 17 0 013 4c0-.6.4-1 1-1h3.5c.6 0 1 .4 1 1 0 1.3.2 2.5.6 3.6.1.3 0 .7-.2 1z" fill="#f78f20"/></svg>
      <span>Help : + 0123-456-7890</span>
    </div>
    <div class="contact-line">
      <svg width="14" height="12" viewBox="0 0 24 20"><rect x="1" y="2" width="22" height="16" fill="#f78f20"/><path d="M1 3l11 8 11-8" fill="none" stroke="#262626" stroke-width="2"/></svg>
      <span>sales@pondermeshpaths<br>.co.uk</span>
    </div>
  </div>

  <div class="footer-col abs" style="left:832px;top:52px">
    <h6>Contact Form</h6>
  </div>
  <div class="form-field abs" style="left:832px;top:93px;width:132px;height:38px">Name</div>
  <div class="form-field abs" style="left:969px;top:93px;width:132px;height:38px">Phone</div>
  <div class="form-field abs" style="left:832px;top:137px;width:269px;height:65px">Message</div>
  <div class="send abs">SEND MESSAGE</div>
</footer>

<div class="bottom-bar abs">
  <p class="copyright abs">© 2016 Pondermeshpaths.All Rights Reserved.</p>
  <div class="pay abs" style="left:736px"></div>
  <div class="pay abs" style="left:786px"></div>
  <div class="pay abs" style="left:836px"></div>
  <div class="pay abs" style="left:886px"></div>
  <div class="social abs" style="left:950px"></div>
  <div class="social abs" style="left:992px"></div>
  <div class="social abs" style="left:1034px"></div>
  <div class="social abs" style="left:1076px"></div>
</div>

</body>
</html>
```